Halvex Power

We need a business card for "Halvex power". I have uploaded the logo, the color of the card should be according to the logo "Blackish".
Basically halvex power is a solar company.
Also we would like a sample file in which we can edit the information such names and contact details ourselves
The card would be two sided with following details
1- logo on front and underneath the logo there should be a line saying
"Cleaner . Cheaper . Power"
2-website i.e "www.halvexpowerco.com"
3- Icons for Facebook and Instagram that tells the clients we are available on both social sites.
4- name of the person with his/her designation underneath and email address
5-contact number
6- 1-800--- number with the extension number

its up to the designer how he/she places the details,but it must look professional

Industry/Entity Type

Business

Contact Information for Business Card

5-contact number

Requirements
Must have
• 1- logo on front and underneath the logo there should be a line saying
• "Cleaner . Cheaper . Power"
• 2-website i.e "www.halvexpowerco.com"
• 3- Icons for Facebook and Instagram that tells the clients we are available on both social sites.
• 4- name of the person with his/her designation underneath and email address
• 5-contact number of the person
• 6- 1-800--- number with the extension number
• 7-card should be in black shade like the logo

```html
<!DOCTYPE html>
<html lang="en">
<head>
<meta charset="utf-8">
<title>Halvex Power – Business Card</title>
<link href="https://fonts.googleapis.com/css2?family=Montserrat:wght@400;500;600;700&display=swap" rel="stylesheet">
<style>
  :root {
    --backdrop: #3b3b3d;
    --card: #1f1f21;
    --emboss: #2b2b2d;
    --emboss-shine: #6c6c70;
    --green: #7ac231;
    --text: #e6e6e6;
    --muted: #bdbdbd;
    --social-a: #2a7fd4;
    --social-b: #c9457f;
  }
  * { margin: 0; padding: 0; box-sizing: border-box; }
  html, body { width: 799px; height: 1200px; overflow: hidden; }
  body {
    background: var(--backdrop);
    font-family: "Montserrat", sans-serif;
    position: relative;
  }
  .card {
    position: absolute;
    left: 100px;
    width: 600px;
    height: 340px;
    background: var(--card);
    border-radius: 3px;
    box-shadow: 0 14px 30px rgba(0,0,0,0.45);
  }
  .card--front { top: 140px; }
  .card--back { top: 720px; }

  .front-mark {
    position: absolute;
    left: 0; right: 0; top: 118px;
    display: flex;
    flex-direction: column;
    align-items: center;
  }
  .front-mark__row {
    display: flex;
    align-items: center;
    gap: 16px;
  }
  .front-mark__dot {
    width: 40px; height: 40px;
    border-radius: 50%;
    background: var(--emboss);
    box-shadow: inset 0 1px 2px rgba(255,255,255,0.08);
  }
  .front-mark__name {
    font-size: 44px;
    font-weight: 600;
    color: var(--emboss-shine);
    letter-spacing: 0.5px;
    line-height: 1.1;
  }
  .front-mark__tagline {
    margin-top: 10px;
    padding-left: 56px;
    font-size: 13px;
    font-weight: 500;
    letter-spacing: 3px;
    color: var(--emboss-shine);
    white-space: nowrap;
  }

  .person { position: absolute; left: 40px; top: 38px; }
  .person__name { color: var(--green); font-weight: 700; font-size: 19px; }
  .person__role { color: var(--text); font-size: 12px; margin-top: 3px; }

  .contact {
    position: absolute; left: 40px; top: 150px;
    color: var(--text); font-size: 14px; line-height: 21px;
    list-style: none;
  }
  .contact li { display: flex; align-items: center; gap: 8px; white-space: nowrap; }
  .contact .no-icon { padding-left: 22px; }
  .contact svg { width: 14px; height: 14px; fill: var(--green); flex: none; }

  .back-mark {
    position: absolute; right: 40px; top: 120px;
    font-size: 34px; font-weight: 700;
    color: var(--green);
  }

  .follow {
    position: absolute; right: 40px; bottom: 30px;
    display: flex; align-items: center; gap: 8px;
    color: var(--text); font-size: 14px;
  }
  .follow__chip { width: 18px; height: 18px; border-radius: 4px; }
  .follow__chip--a { background: var(--social-a); }
  .follow__chip--b { background: var(--social-b); }
</style>
</head>
<body>
  <section class="card card--front" aria-label="Card front">
    <div class="front-mark">
      <div class="front-mark__row">
        <span class="front-mark__dot"></span>
        <span class="front-mark__name">Halvex Power</span>
      </div>
      <p class="front-mark__tagline">Cleaner . Cheaper . Power</p>
    </div>
  </section>

  <section class="card card--back" aria-label="Card back">
    <div class="person">
      <p class="person__name">Marek D. Olsen</p>
      <p class="person__role">Solar Sales Consultant</p>
    </div>

    <ul class="contact">
      <li class="no-icon">14 Prairie Ridge Road</li>
      <li class="no-icon">Westfield K7L 2M9</li>
      <li>
        <svg viewBox="0 0 16 16" aria-hidden="true"><path d="M3.5 1l2.5 3-1.5 2c1 2 3 4 5 5l2-1.5 3 2.5-1.5 2.5C7 15 1 9 1 2.5z"/></svg>
        1- 833-555-0142 Ext. 204
      </li>
      <li>
        <svg viewBox="0 0 16 16" aria-hidden="true"><path d="M1 3h14v10H1z M2 4l6 5 6-5" fill="none" stroke="#7ac231" stroke-width="1.6"/></svg>
        info@halvexpowerco.com
      </li>
      <li>
        <svg viewBox="0 0 16 16" aria-hidden="true"><circle cx="8" cy="8" r="6.5" fill="none" stroke="#7ac231" stroke-width="1.5"/><path d="M1.5 8h13M8 1.5c-3 3-3 10 0 13M8 1.5c3 3 3 10 0 13" fill="none" stroke="#7ac231" stroke-width="1.2"/></svg>
        www.halvexpowerco.com
      </li>
    </ul>

    <p class="back-mark">Halvex Power</p>

    <div class="follow">
      <span>Follow on:</span>
      <span class="follow__chip follow__chip--a"></span>
      <span class="follow__chip follow__chip--b"></span>
    </div>
  </section>
</body>
</html>
```